Business Card: RW Office Partners - Your organised problem solver

Business Name: RW Office Partners
Website: www.rwofficepartners.com.au
Email: marisol@rwofficepartners.com.au
Mobile: 61 482 907 236
Facebook: @rwofficepartners
Instrgram: @rwofficepartners

Brading Colours:
HEX
#986474
#ddccd3
#7a8498
#c9d8e4
#000000
#ffffff

Tag Line: Your organised problem solver

Link to DRAFT website:
https://deskhelpcollective.wixsite.com/rw-office-partners

About Page from the website:
My name is Marisol Wrenfield, and I would love to assist you to become more productive in your day to day and achieve your business and personal goals.
My mission is to give you time, time to work on the important tasks of your business or to be able to spend more time with your family. I will take on the tasks you don’t have time for, don’t know well or simply don’t like to do.
I have an extensive background in Administration, Tender Coordination, Document Control, WHS and Quality Management working primarily in the Construction, Mining and Corporate World.
I am passionate about being organised, having order and making things in your life (and mine) easier! I love to watch something unfold and grow into something amazing! I am known for being the go-to problem solver, the organiser of all things, producing high standards of work even under pressure. I’m also a confident communicator, and I understand that you’re busy running your business.

Target Market(s)

Small to Medium Business who require assistance in their business by a virtual assistant.

Industry/Entity Type

Virtual Assistant

Contact Information for Business Card

Mobile: 61 482 907 236

Font styles to use
Sans Serif

Colors
ffffff

Requirements
Must have
• Branding Colours as outlined.
Contact Details as outlined.
Logo as provided.
Proper contact details - mobile, facebook, instragm, website.
Simple, Elegant, very clean looking.
Should not have
• Note cute with pictures.
Not too girly as still want to market to construction companies.

```html
<!DOCTYPE html>
<html lang="en">
<head>
<meta charset="utf-8">
<title>RW Office Partners – Business Card</title>
<link rel="stylesheet" href="https://fonts.googleapis.com/css2?family=Montserrat:wght@500&family=Montserrat+Alternates:wght@700&family=Arimo:wght@400&display=swap">
<style>
  :root {
    --plum: #986474;
    --blush: #ddccd3;
    --slate: #7a8498;
    --mist: #c9d8e4;
    --ink: #000000;
    --paper: #ffffff;
    --backdrop: #e9ecf1;
  }
  html, body {
    margin: 0;
    width: 1200px;
    height: 909px;
    overflow: hidden;
    background: var(--backdrop);
  }
  .canvas {
    position: relative;
    width: 1200px;
    height: 909px;
  }
  .card {
    position: absolute;
    left: 250px;
    width: 700px;
    height: 400px;
    border-radius: 26px;
    overflow: hidden;
    box-shadow: 0 6px 18px rgba(40, 48, 66, 0.18);
  }
  .card--front { top: 36px; background: var(--slate); }
  .card--back  { top: 473px; background: var(--paper); }

  .brand {
    position: absolute;
    display: flex;
    align-items: center;
    gap: 14px;
    font-family: "Montserrat", sans-serif;
    font-weight: 500;
    text-transform: uppercase;
    letter-spacing: 2px;
    white-space: nowrap;
  }
  .brand__mark { width: 18px; height: 18px; background: var(--plum); }
  .card--front .brand { left: 50%; top: 120px; transform: translateX(-50%); font-size: 40px; color: var(--paper); }
  .card--back .brand  { right: 50px; top: 62px; font-size: 28px; color: var(--slate); }

  .rule { position: absolute; height: 1.5px; }
  .card--front .rule { background: var(--paper); }
  .rule--upper { right: 0; top: 228px; width: 250px; }
  .rule--lower { left: 0; top: 300px; width: 205px; }
  .tagline {
    position: absolute;
    left: 220px;
    top: 288px;
    font-family: "Arimo", sans-serif;
    font-size: 19px;
    letter-spacing: 0.5px;
    color: var(--paper);
  }

  .card--back .rule { background: var(--slate); }
  .rule--divider { left: 225px; top: 264px; width: 425px; }
  .rule--short { left: 60px; top: 298px; width: 270px; }

  .person { position: absolute; left: 60px; top: 212px; }
  .person__name {
    margin: 0;
    font-family: "Montserrat Alternates", sans-serif;
    font-weight: 700;
    font-size: 30px;
    line-height: 38px;
    color: var(--plum);
  }
  .person__role {
    margin: 2px 0 0;
    font-family: "Arimo", sans-serif;
    font-size: 19px;
    line-height: 24px;
    color: var(--slate);
  }

  .contacts {
    position: absolute;
    left: 60px;
    top: 312px;
    margin: 0;
    padding: 0;
    list-style: none;
    font-family: "Arimo", sans-serif;
    font-size: 17px;
    color: #333;
  }
  .contacts li { display: flex; align-items: center; gap: 10px; height: 24px; }
  .contacts svg { width: 13px; height: 13px; fill: var(--plum); }

  .socials {
    position: absolute;
    right: 50px;
    top: 278px;
    margin: 0;
    padding: 0;
    list-style: none;
    font-family: "Arimo", sans-serif;
    font-size: 17px;
    color: #333;
    text-align: right;
  }
  .socials li { display: flex; align-items: center; justify-content: flex-end; gap: 10px; height: 30px; }
  .socials__dot { width: 12px; height: 12px; background: var(--plum); border-radius: 2px; }
</style>
</head>
<body>
<main class="canvas">

  <section class="card card--front" aria-label="Card front">
    <div class="brand"><span class="brand__mark"></span>RW Office Partners</div>
    <div class="rule rule--upper"></div>
    <div class="rule rule--lower"></div>
    <p class="tagline">Your organised problem solver</p>
  </section>

  <section class="card card--back" aria-label="Card back">
    <div class="brand"><span class="brand__mark"></span>RW Office Partners</div>
    <div class="rule rule--divider"></div>

    <div class="person">
      <h1 class="person__name">Dorian L. Vasquez</h1>
      <p class="person__role">Project Manager</p>
    </div>
    <div class="rule rule--short"></div>

    <ul class="contacts">
      <li>
        <svg viewBox="0 0 24 24" aria-hidden="true"><path d="M6.6 10.8a15.2 15.2 0 0 0 6.6 6.6l2.2-2.2a1 1 0 0 1 1-.25 11.4 11.4 0 0 0 3.6.57 1 1 0 0 1 1 1V20a1 1 0 0 1-1 1A17 17 0 0 1 3 4a1 1 0 0 1 1-1h3.5a1 1 0 0 1 1 1c0 1.25.2 2.45.57 3.6a1 1 0 0 1-.25 1z"/></svg>
        61 482 907 236
      </li>
      <li>
        <svg viewBox="0 0 24 24" aria-hidden="true"><path d="M2 5h20v14H2z M2 5l10 8 10-8" /></svg>
        marisol@rwofficepartners.com.au
      </li>
      <li>
        <svg viewBox="0 0 24 24" aria-hidden="true"><circle cx="12" cy="12" r="10"/></svg>
        www.rwofficepartners.com.au
      </li>
    </ul>

    <ul class="socials">
      <li>@rwofficepartners <span class="socials__dot"></span></li>
      <li>@rwofficepartners <span class="socials__dot"></span></li>
    </ul>
  </section>

</main>
</body>
</html>
```